Harborlight Amusement Collective (HAC)

We need a business card design for Harborlight Amusement Collective. Modern and sleek looking, with all critical information. Open to single or double sided designs, if double sided info needs to be all on one side. The main Logo is Harborlight Amusement collective and must be on the card. The other three logos are for the brands that fall under the group, they might be good on the back.

Industry/Entity Type

Business

```html
<!DOCTYPE html>
<html lang="en">
<head>
<meta charset="utf-8">
<title>Harborlight Amusement Collective – Business Card</title>
<link rel="stylesheet" href="https://fonts.googleapis.com/css2?family=Montserrat:wght@500;600&family=Source+Sans+3:wght@400;600;700&display=swap">
<style>
  :root {
    --backdrop: #3b3b3b;
    --card-front: #ececec;
    --brand-blue: #1f4e96;
    --brand-green: #8a9f2f;
    --ink: #3a3a3a;
    --rule: #9a9a9a;
    --white: #ffffff;
  }
  * { box-sizing: border-box; margin: 0; padding: 0; }
  html, body {
    width: 1200px; height: 900px; overflow: hidden;
    background: var(--backdrop);
  }
  .stage { position: relative; width: 1200px; height: 900px; }

  .card {
    position: absolute; top: 170px;
    width: 347px; height: 561px;
    overflow: hidden;
  }
  .card--front { left: 259px; background: var(--card-front); }
  .card--back { left: 631px; }

  /* Front */
  .front {
    display: flex; flex-direction: column; align-items: center;
    padding-top: 60px; text-align: center;
    font-family: "Source Sans 3", sans-serif; color: var(--ink);
  }
  .brand-mark {
    width: 62px; height: 62px; background: var(--brand-blue);
  }
  .wordmark {
    margin-top: 22px;
    font-family: "Montserrat", sans-serif; font-weight: 600;
    color: var(--brand-blue); line-height: 1;
  }
  .wordmark__line1 { display: block; font-size: 19px; }
  .wordmark__line2 { display: block; font-size: 18px; letter-spacing: 6px; margin-top: 10px; }

  .person { margin-top: 34px; }
  .person__name { font-size: 21px; font-weight: 400; letter-spacing: 0.5px; line-height: 1.1; }
  .person__first { color: var(--brand-blue); }
  .person__last { color: var(--brand-green); }
  .person__title { font-size: 15.5px; margin-top: 2px; }

  .rule { width: 170px; height: 1px; background: var(--rule); margin: 10px auto; }

  .contact { list-style: none; font-size: 15.5px; line-height: 20.5px; }
  .contact__label { color: var(--brand-blue); font-weight: 700; }
  .contact__web { font-weight: 700; color: var(--brand-blue); }
  .contact__web span { color: var(--brand-green); }

  .address { font-size: 15.5px; line-height: 20px; }

  .sub-brands {
    margin-top: 10px; display: flex; flex-wrap: wrap; justify-content: center;
    column-gap: 22px; row-gap: 14px; width: 320px;
  }
  .sub-brand {
    display: flex; align-items: center; gap: 6px;
    font-family: "Source Sans 3", sans-serif; font-weight: 700;
    font-size: 19px; line-height: 1;
  }
  .sub-brand__dot { width: 20px; height: 20px; border-radius: 50%; }
  .sub-brand--quayside { color: #1d1d1d; }
  .sub-brand--quayside .sub-brand__dot { background: var(--brand-blue); }
  .sub-brand--gatepass { color: var(--brand-blue); }
  .sub-brand--gatepass .sub-brand__dot { background: var(--brand-blue); }
  .sub-brand--seats { color: var(--brand-blue); }
  .sub-brand--seats .sub-brand__dot { background: var(--brand-green); }

  /* Back */
  .back-art {
    position: absolute; inset: 0;
    background:
      linear-gradient(155deg, var(--brand-green) 0%, #4f7a76 30%, var(--brand-blue) 55%, #5b7d6a 75%, var(--brand-green) 100%);
  }
  .back-wordmark {
    position: absolute; left: 0; right: 0; top: 445px;
    text-align: center; color: var(--white);
    font-family: "Montserrat", sans-serif; font-weight: 600; line-height: 1;
  }
  .back-wordmark__line1 { display: block; font-size: 19px; }
  .back-wordmark__line2 { display: block; font-size: 18px; letter-spacing: 6px; margin-top: 11px; }
</style>
</head>
<body>
<main class="stage">

  <section class="card card--front" aria-label="Card front">
    <div class="front">
      <div class="brand-mark" aria-hidden="true"></div>
      <h1 class="wordmark">
        <span class="wordmark__line1">HARBORLIGHT AMUSEMENT</span>
        <span class="wordmark__line2">COLLECTIVE</span>
      </h1>

      <div class="person">
        <p class="person__name"><span class="person__first">DANIEL</span> <span class="person__last">REEVES</span></p>
        <p class="person__title">Managing Director</p>
      </div>

      <div class="rule"></div>

      <ul class="contact">
        <li><span class="contact__label">P:</span> 044-987 654 321</li>
        <li><span class="contact__label">M:</span> 044-987 654 320</li>
        <li><span class="contact__label">E:</span> hello@harborlightac.com</li>
        <li class="contact__web">www.<span>harborlightac</span>.com</li>
      </ul>

      <div class="rule"></div>

      <address class="address" style="font-style: normal;">
        48 Wharf Lane, Suite 3<br>
        Seabrook, 204519.
      </address>

      <div class="rule"></div>

      <div class="sub-brands">
        <span class="sub-brand sub-brand--quayside"><span class="sub-brand__dot"></span>Quayside Hospitality</span>
        <span class="sub-brand sub-brand--gatepass"><span class="sub-brand__dot"></span>gatepass</span>
        <span class="sub-brand sub-brand--seats"><span class="sub-brand__dot"></span>HarborSeats</span>
      </div>
    </div>
  </section>

  <section class="card card--back" aria-label="Card back">
    <div class="back-art" role="img" aria-label="Large brand monogram pattern in blue and green"></div>
    <p class="back-wordmark">
      <span class="back-wordmark__line1">HARBORLIGHT AMUSEMENT</span>
      <span class="back-wordmark__line2">COLLECTIVE</span>
    </p>
  </section>

</main>
</body>
</html>
```